we can communicate on this, but i want to follow the approach we took on Pellew|Marsh & Quinlan but i feel the card front needs the black background and the platinum and gold logo. The back? I am open. we can use the same info from PM&Q. Velmont Arc is an enhanced equity investment fund - basically a very exclusive boutique hedge fund that uses only stock options. very advanced things. hope you are interested

Contact Information for Business Card

Dr. Lewis T. Brennick, CFA
Scientifique de fusée financière
701.555.0143
LTBquant47@mailvantor.com

4718 Willow Creek Bend W.
West Fargo, ND 58078

No web site

Colors

Designer to choose colors to be used in the design.

Requirements
Nice to have
• I tend to prefer the most visible applications of the logo to include logo and name, the logo version with a black background and the gold and platinum components separated by the black. I see this working well for a single side (logo and name - this is card front to me).
• I am fairly open to other treatments on the reverse side with the data. To me, it makes sense to have a different color rendition of the logo on the reverse and it may be a muted black tone on tone or an oversized portion that would have spot UV. Or, the reverse may play with colors and layout
Should not have
• Other colors = no no
• Decorative font

```html
<!DOCTYPE html>
<html lang="en">
<head>
<meta charset="utf-8">
<title>Velmont Arc — Business Card</title>
<link href="https://fonts.googleapis.com/css2?family=Roboto:ital,wght@0,400;0,500;0,700;1,400&display=swap" rel="stylesheet">
<style>
  :root {
    --backdrop: #1c1c1d;
    --card-black: #1d1e20;
    --gold: #d4b043;
    --gold-deep: #c39b34;
    --gold-light: #e0c154;
    --platinum: #d9d9dc;
    --platinum-dark: #8e8e92;
    --white: #ffffff;
  }
  * { box-sizing: border-box; margin: 0; padding: 0; }
  html, body {
    width: 1200px; height: 800px; overflow: hidden;
    background: var(--backdrop);
    font-family: "Roboto", Arial, sans-serif;
  }
  .sheet {
    width: 1200px; height: 800px;
    display: flex; align-items: center; justify-content: center; gap: 40px;
  }
  .card {
    position: relative; width: 540px; height: 309px;
    background: var(--card-black); overflow: hidden;
    box-shadow: 0 10px 30px rgba(0,0,0,.45);
  }
  /* front */
  .card-front .brand {
    position: absolute; inset: 0;
    display: flex; flex-direction: column; align-items: center; justify-content: center; gap: 18px;
  }
  .brand-mark {
    width: 92px; height: 92px; border-radius: 50%;
    background: linear-gradient(135deg, var(--platinum) 0%, var(--platinum-dark) 100%);
  }
  .brand-name {
    font-weight: 700; font-size: 34px; letter-spacing: 2px;
    color: var(--platinum); text-transform: uppercase; line-height: 1;
  }
  /* back */
  .card-back .wave { position: absolute; inset: 0; width: 100%; height: 100%; }
  .card-back .brand {
    position: absolute; left: 40px; top: 62px; width: 190px;
    display: flex; flex-direction: column; align-items: center; gap: 12px;
  }
  .card-back .brand-mark {
    width: 58px; height: 58px;
    background: linear-gradient(135deg, var(--gold-light) 0%, var(--gold-deep) 100%);
  }
  .card-back .brand-name { font-size: 22px; color: var(--white); letter-spacing: 1.5px; }
  .contact {
    position: absolute; right: 28px; top: 122px;
    text-align: right; color: var(--white);
  }
  .contact-name { font-weight: 700; font-size: 17px; line-height: 1.1; }
  .contact-name .credential { font-size: 10px; font-weight: 500; }
  .contact-title { font-style: italic; font-size: 10.5px; margin-top: 2px; }
  .contact-address { font-size: 10.5px; line-height: 1.35; margin-top: 12px; }
  .contact-lines { list-style: none; font-size: 10.5px; line-height: 1.5; margin-top: 10px; }
  .contact-lines li { display: flex; align-items: center; justify-content: flex-end; gap: 6px; }
  .contact-lines svg { width: 9px; height: 9px; fill: var(--white); flex: none; }
</style>
</head>
<body>
<main class="sheet">
  <section class="card card-front" aria-label="Card front">
    <div class="brand">
      <span class="brand-mark"></span>
      <span class="brand-name">Velmont Arc</span>
    </div>
  </section>

  <section class="card card-back" aria-label="Card back">
    <svg class="wave" viewBox="0 0 540 309" preserveAspectRatio="none" aria-hidden="true">
      <defs>
        <linearGradient id="goldFill" x1="0" y1="1" x2="1" y2="0">
          <stop offset="0" stop-color="#e0c154"/>
          <stop offset="1" stop-color="#c49b37"/>
        </linearGradient>
      </defs>
      <path d="M0,236 C150,268 220,236 280,140 C340,46 420,28 540,22"
            fill="none" stroke="#d9d9dc" stroke-width="9"/>
      <path d="M0,246 C160,278 228,246 290,150 C350,56 428,38 540,32 L540,309 L0,309 Z"
            fill="url(#goldFill)" stroke="#111" stroke-width="2"/>
    </svg>

    <div class="brand">
      <span class="brand-mark"></span>
      <span class="brand-name">Velmont Arc</span>
    </div>

    <div class="contact">
      <p class="contact-name">Dr. Lewis T. Brennick, <span class="credential">CFA</span></p>
      <p class="contact-title">Scientifique de fusée financière</p>
      <p class="contact-address">4718 Willow Creek Bend W.<br>West Fargo, ND 58078</p>
      <ul class="contact-lines">
        <li>701.555.0143
          <svg viewBox="0 0 10 10"><rect x="2.5" y="0" width="5" height="10" rx="1"/></svg></li>
        <li>LTBquant47@mailvantor.com
          <svg viewBox="0 0 10 10"><path d="M0 2h10v6H0z M0 2l5 3.5L10 2"/></svg></li>
      </ul>
    </div>
  </section>
</main>
</body>
</html>
```